Retail Jewelry Business Card Design Project

We are in need of a new business card design for a retail jewelry store. This store is in the business of fine jewelry including but not specific to bridal jewelry, diamonds, designer jewelry and watches.

This store has been in business for 20 years but continues to strive for a modern professional appeal. The main colors use for this business are a royal blue, white and silver.

Target Market(s)

Target market is ages 18-50

Industry/Entity Type

Jewelry

Requirements
Must have
• Sales Person Name
Sales Person Email Address

Store Address
Store Phone
Website

Standard business card size. No odd shapes or sizes.
Nice to have
• Overall modern feel for card.

We have thought that a design with a nice feature of the logo on the back of the card would be nice but open to ideas.
Should not have
• No specific images of jewelry should be used.

```html
<!DOCTYPE html>
<html lang="en">
<head>
<meta charset="utf-8">
<title>Marlow Reid Fine Jewelry – Business Card</title>
<link rel="stylesheet" href="https://fonts.googleapis.com/css2?family=Questrial&display=swap">
<style>
  :root {
    --royal-blue: #2e3690;
    --lavender: #7870b0;
    --white: #ffffff;
    --stage: #e9e9ee;
    --card-shadow: rgba(20, 20, 40, 0.18);
  }
  * { box-sizing: border-box; margin: 0; padding: 0; }
  html, body {
    width: 1200px;
    height: 700px;
    overflow: hidden;
    background: var(--stage);
    font-family: "Questrial", "Century Gothic", sans-serif;
  }
  .canvas {
    width: 1200px;
    height: 700px;
    display: flex;
    align-items: center;
    justify-content: center;
    gap: 50px;
  }
  .card {
    width: 525px;
    height: 300px;
    position: relative;
    overflow: hidden;
    box-shadow: 0 6px 18px var(--card-shadow);
  }

  /* Front */
  .card--front { background: var(--white); }
  .front__brand {
    position: absolute;
    top: 0; left: 0; right: 0;
    height: 150px;
    display: flex;
    flex-direction: column;
    align-items: center;
    justify-content: center;
    color: var(--royal-blue);
  }
  .brand-name {
    font-size: 50px;
    line-height: 1;
    letter-spacing: 1px;
  }
  .brand-tagline {
    font-size: 22px;
    letter-spacing: 4px;
    margin-top: 10px;
  }
  .front__name-band {
    position: absolute;
    top: 150px; left: 0; right: 0;
    height: 52px;
    background: var(--lavender);
    color: var(--white);
    display: flex;
    align-items: center;
    justify-content: center;
    font-size: 21px;
    letter-spacing: 1.5px;
    text-transform: uppercase;
  }
  .front__contact {
    position: absolute;
    top: 206px; left: 0; right: 0; bottom: 0;
    background: var(--royal-blue);
    color: var(--white);
    display: flex;
    flex-direction: column;
    align-items: center;
    justify-content: center;
    gap: 12px;
    font-size: 14px;
    letter-spacing: 0.5px;
  }
  .contact-row { display: flex; align-items: center; gap: 18px; }
  .contact-item { display: flex; align-items: center; gap: 6px; }
  .contact-icon { width: 13px; height: 13px; fill: var(--white); }

  /* Back */
  .card--back {
    background: var(--royal-blue);
    color: var(--white);
    display: flex;
    flex-direction: column;
    align-items: center;
    justify-content: center;
  }
  .card--back .brand-name { font-size: 56px; }
  .card--back .brand-tagline { font-size: 24px; }
  .back__website {
    margin-top: 40px;
    font-size: 15px;
    letter-spacing: 3px;
  }
</style>
</head>
<body>
  <main class="canvas">
    <section class="card card--front" aria-label="Business card front">
      <div class="front__brand">
        <div class="brand-name">Marlow Reid</div>
        <div class="brand-tagline">FINE JEWELRY</div>
      </div>
      <div class="front__name-band">Marlow Reid Hartley</div>
      <div class="front__contact">
        <div class="contact-row">
          <span class="contact-item">
            <svg class="contact-icon" viewBox="0 0 24 24" aria-hidden="true"><path d="M6.6 10.8a15.2 15.2 0 0 0 6.6 6.6l2.2-2.2a1 1 0 0 1 1-.25 11.4 11.4 0 0 0 3.6.57 1 1 0 0 1 1 1V20a1 1 0 0 1-1 1A17 17 0 0 1 3 4a1 1 0 0 1 1-1h3.5a1 1 0 0 1 1 1c0 1.25.2 2.45.57 3.57a1 1 0 0 1-.25 1z"/></svg>
            555-218-0147
          </span>
          <span class="contact-item">
            <svg class="contact-icon" viewBox="0 0 24 24" aria-hidden="true"><path d="M2 5h20v14H2z M2 5l10 8 10-8" fill="none" stroke="#fff" stroke-width="2"/></svg>
            marlow@marlowreidjewelry.com
          </span>
        </div>
        <div class="contact-address">2380 Carden Street, Bay Harbor, FL 32499</div>
      </div>
    </section>

    <section class="card card--back" aria-label="Business card back">
      <div class="brand-name">Marlow Reid</div>
      <div class="brand-tagline">FINE JEWELRY</div>
      <div class="back__website">www.marlowreidjewelry.com</div>
    </section>
  </main>
</body>
</html>
```